Hair salon Business Card

Beauty Salon
I would like to see designs using sky blue and a soft orange. Mainly I would like my name ( Amberly Salon ) used as the design

Industry/Entity Type

Business

Contact Information for Business Card

Amberly Salon
318 E Maple Hyw #14
Alder Springs, Ca 91904
909 555-2716

```html
<!DOCTYPE html>
<html lang="en">
<head>
<meta charset="utf-8">
<title>Amberly Salon — Business Card</title>
<link href="https://fonts.googleapis.com/css2?family=Questrial&family=Open+Sans:wght@400&display=swap" rel="stylesheet">
<style>
  :root {
    --stage: #000000;
    --card: #ffffff;
    --sky-blue: #1a4fb0;
    --soft-orange: #d07c0a;
    --pale-peach: #f5e5d1;
    --ink: #1a1a1a;
  }
  html, body {
    margin: 0;
    padding: 0;
    width: 1200px;
    height: 900px;
    overflow: hidden;
    background: var(--stage);
  }
  .canvas {
    position: relative;
    width: 1200px;
    height: 900px;
  }
  .card {
    position: absolute;
    top: 275px;
    width: 477px;
    height: 293px;
    background: var(--card);
    overflow: hidden;
  }
  .card--front {
    left: 116px;
    border-radius: 0 50px 0 50px;
  }
  .card--back {
    left: 622px;
    border-radius: 50px 0 50px 0;
  }
  .card__art {
    position: absolute;
    left: 0;
    top: 0;
    height: 293px;
  }
  .wordmark {
    position: absolute;
    font-family: "Questrial", sans-serif;
    font-weight: 400;
    color: var(--sky-blue);
    text-align: center;
    line-height: 1;
  }
  .wordmark__name { display: block; white-space: nowrap; }
  .wordmark__tag { display: block; letter-spacing: 0.06em; }
  .card--front .wordmark {
    right: 76px;
    top: 51px;
  }
  .card--front .wordmark__name { font-size: 29px; }
  .card--front .wordmark__tag { font-size: 13px; margin-top: 5px; }
  .wordmark-dot {
    position: absolute;
    right: 34px;
    top: 56px;
    width: 22px;
    height: 22px;
    border-radius: 50%;
    background: var(--soft-orange);
  }
  .card--back .wordmark {
    right: 48px;
    top: 218px;
  }
  .card--back .wordmark__name { font-size: 32px; }
  .card--back .wordmark__tag { font-size: 14px; margin-top: 5px; }
  .contact {
    position: absolute;
    right: 28px;
    font-family: "Open Sans", sans-serif;
    font-size: 12.5px;
    color: var(--ink);
    text-align: right;
    line-height: 20px;
    margin: 0;
  }
  .contact--phone {
    top: 180px;
    display: flex;
    align-items: center;
    gap: 4px;
  }
  .contact--address { top: 219px; font-style: normal; }
  .phone-icon { width: 10px; height: 10px; }
</style>
</head>
<body>
<div class="canvas">
  <section class="card card--front">
    <svg class="card__art" width="200" height="293" viewBox="0 0 200 293" role="img" aria-label="Pale peach profile illustration of a woman with swept hair">
      <path d="M0 0 H100 C150 50 178 120 172 200 C168 245 150 272 55 293 H0 Z" fill="var(--pale-peach)"/>
    </svg>
    <div class="wordmark">
      <span class="wordmark__name">Amberly</span>
      <span class="wordmark__tag">SALON</span>
    </div>
    <span class="wordmark-dot"></span>
    <p class="contact contact--phone">909 555-2716
      <svg class="phone-icon" viewBox="0 0 24 24" aria-hidden="true">
        <path fill="var(--soft-orange)" d="M6.6 10.8a15.1 15.1 0 0 0 6.6 6.6l2.2-2.2a1 1 0 0 1 1-.25 11.4 11.4 0 0 0 3.6.57 1 1 0 0 1 1 1V20a1 1 0 0 1-1 1A17 17 0 0 1 3 4a1 1 0 0 1 1-1h3.5a1 1 0 0 1 1 1c0 1.25.2 2.450.57 3.6a1 1 0 0 1-.25 1z"/>
      </svg>
    </p>
    <address class="contact contact--address">318 E Maple Hyw #14<br>Alder Springs, Ca 91904</address>
  </section>

  <section class="card card--back">
    <svg class="card__art" width="200" height="293" viewBox="0 0 200 293" role="img" aria-label="Orange profile illustration of a woman with swept hair">
      <path d="M0 0 H110 C150 50 168 120 162 200 C158 245 145 272 50 293 H0 Z" fill="var(--soft-orange)"/>
    </svg>
    <div class="wordmark">
      <span class="wordmark__name">Amberly</span>
      <span class="wordmark__tag">SALON</span>
    </div>
  </section>
</div>
</body>
</html>
```